Bright Harbor Counseling Letterhead for hip modern business

I would like some ombre use of the colors in the logo hip letterhead that incorporates logo colors and feel, needs to connect with young professionals and college students. i need to be able to write letters to schools to excuse absences as well. i like color blocks on one side preferably using colors from the attached logo design.

Target Market(s)

high income young people, young adults and college students

Industry/Entity Type

mental health

Font styles to use
Serif
Sans Serif

Colors
0054AA
0677BA
7BADD7
CADEEF
E8F1F8
0094D4
00A9DD
6FCCEA
C7EBF8
E9F6FB
00AB8E
00BBA5
67D7C9
C6EFE9
E9F9F6
59FF00
82FF00
B8FF75
E3FFCB
F4FFEA
A7469A
B969AE
D3A5CF
EDDBEB
F8F0F9
6B429C
8869AF
B7A5CE
E3DAEB
F3F0F8

Requirements
Must have
• a modern hip feel, somewhat color

```html
<!DOCTYPE html>
<html lang="en">
<head>
<meta charset="utf-8">
<title>Bright Harbor Counseling Letterhead</title>
<link rel="stylesheet" href="https://fonts.googleapis.com/css2?family=Open+Sans:wght@300;400;700&display=swap">
<style>
  :root {
    --backdrop: #e4ddf3;
    --paper: #fdf2fb;
    --paper-glow: #ffffff;
    --plum: #a7469a;
    --plum-deep: #8a2f86;
    --orchid: #b969ae;
    --violet: #6b429c;
    --sky: #6fcbea;
    --teal: #00bba5;
    --ink: #3a3a3a;
    --ink-soft: #555555;
    --rule: #d9cfe0;
  }
  * { box-sizing: border-box; margin: 0; padding: 0; }
  html, body { width: 1200px; height: 784px; overflow: hidden; }
  body {
    background: var(--backdrop);
    font-family: "Open Sans", Arial, sans-serif;
    position: relative;
  }
  .letterhead {
    position: absolute;
    left: 338px; top: 22px;
    width: 523px; height: 740px;
    background: radial-gradient(ellipse at 55% 45%, var(--paper-glow) 0%, var(--paper) 70%);
    box-shadow: 0 6px 18px rgba(90, 70, 130, 0.18);
    overflow: hidden;
  }
  .color-blocks { position: absolute; inset: 0; width: 100%; height: 100%; }

  .brand {
    position: absolute;
    left: 34px; top: 34px;
    display: flex; align-items: flex-end; gap: 10px;
    color: var(--ink);
  }
  .brand-name { font-weight: 300; line-height: 1; }
  .brand-name .line-main { display: block; font-size: 27px; letter-spacing: 0.2px; }
  .brand-name .line-sub { display: block; font-size: 12px; letter-spacing: 3.2px; text-align: right; margin-top: 5px; }
  .brand-dot {
    width: 22px; height: 22px; border-radius: 50%;
    background: var(--plum);
    margin-bottom: 2px;
  }

  .contact {
    position: absolute;
    left: 160px; top: 108px;
    padding-left: 14px;
    border-left: 1px solid var(--rule);
    font-size: 7.5px;
    line-height: 1.55;
    color: var(--ink-soft);
    list-style: none;
  }
  .contact li { display: flex; align-items: flex-start; gap: 5px; }
  .contact .address { color: var(--plum-deep); font-weight: 700; }
  .contact-icon { width: 9px; height: 9px; flex: none; margin-top: 2px; }
</style>
</head>
<body>
  <main class="letterhead">
    <svg class="color-blocks" viewBox="0 0 523 740" aria-hidden="true">
      <defs>
        <linearGradient id="ombre-plum" x1="0" y1="0" x2="1" y2="1">
          <stop offset="0" stop-color="#d3a5cf"/>
          <stop offset="0.5" stop-color="#b969ae"/>
          <stop offset="1" stop-color="#6b429c"/>
        </linearGradient>
        <linearGradient id="ombre-sea" x1="0" y1="0" x2="1" y2="0">
          <stop offset="0" stop-color="#6fccea"/>
          <stop offset="1" stop-color="#00bba5"/>
        </linearGradient>
      </defs>
      <g class="block-top-right">
        <rect x="493" y="0" width="30" height="150" fill="url(#ombre-plum)"/>
        <rect x="481" y="0" width="8" height="112" fill="url(#ombre-sea)"/>
        <rect x="473" y="0" width="4" height="80" fill="#b7a5ce"/>
      </g>
      <g class="block-bottom-left">
        <rect x="0" y="590" width="30" height="150" fill="url(#ombre-plum)"/>
        <rect x="34" y="628" width="8" height="112" fill="url(#ombre-sea)"/>
        <rect x="46" y="660" width="4" height="80" fill="#b7a5ce"/>
      </g>
    </svg>

    <header class="brand">
      <h1 class="brand-name">
        <span class="line-main">Bright Harbor</span>
        <span class="line-sub">Counseling</span>
      </h1>
      <span class="brand-dot" aria-hidden="true"></span>
    </header>

    <ul class="contact">
      <li class="address">
        <svg class="contact-icon" viewBox="0 0 10 10" aria-hidden="true"><circle cx="5" cy="5" r="5" fill="var(--plum)"/><path d="M5 2.2a1.8 1.8 0 0 1 1.8 1.8C6.8 5.4 5 7.8 5 7.8S3.2 5.4 3.2 4A1.8 1.8 0 0 1 5 2.2z" fill="#fff"/></svg>
        <span>2210 Harbor Row, Ste 48,<br>Oregon, 97204, United States</span>
      </li>
      <li>
        <svg class="contact-icon" viewBox="0 0 10 10" aria-hidden="true"><circle cx="5" cy="5" r="5" fill="var(--plum)"/><path d="M3.3 2.5l1 1-.5.8c.4.8.9 1.3 1.7 1.7l.8-.5 1 1-.6.9C4.6 7.2 2.8 5.4 2.6 3.1z" fill="#fff"/></svg>
        <span>(000) 000-0000</span>
      </li>
      <li>
        <svg class="contact-icon" viewBox="0 0 10 10" aria-hidden="true"><circle cx="5" cy="5" r="5" fill="var(--plum)"/><rect x="2.8" y="3" width="4.4" height="4" fill="#fff"/><rect x="3.5" y="3.7" width="3" height="1.2" fill="var(--plum)"/></svg>
        <span>(000) 000-0000</span>
      </li>
      <li>
        <svg class="contact-icon" viewBox="0 0 10 10" aria-hidden="true"><circle cx="5" cy="5" r="5" fill="var(--plum)"/><rect x="2.5" y="3.2" width="5" height="3.6" fill="#fff"/><path d="M2.5 3.2L5 5.2l2.5-2" fill="none" stroke="var(--plum)" stroke-width=".6"/></svg>
        <span>hello@brightharborcounsel.com</span>
      </li>
      <li>
        <svg class="contact-icon" viewBox="0 0 10 10" aria-hidden="true"><circle cx="5" cy="5" r="5" fill="var(--orchid)"/><circle cx="5" cy="5" r="2.6" fill="none" stroke="#fff" stroke-width=".6"/><path d="M2.4 5h5.2M5 2.4c-1.2 1.5-1.2 3.7 0 5.2M5 2.4c1.2 1.5 1.2 3.7 0 5.2" fill="none" stroke="#fff" stroke-width=".5"/></svg>
        <span>www.brightharborcounsel.com</span>
      </li>
    </ul>
  </main>
</body>
</html>
```